Re-Design an adult education portal

I need support to re-design an adult education portal. Currently the customer has an incomplete website which should be prepared in a new format.
I have the idea how to realize, but I have no clue how to design it. The hard thing is to have a "beautiful" website with available logo and main color. I hope you can support me.

Name of Website: moluvo (moluvo.ch)
Content: adult eduction for adult in safety at work, mountain climbing, dog school. various courses in different areas. But on old webpage is hard to find the different possibilities.
main color: Ral 6011 (green) -> #6C7C59
logo: you see on top of website the logo (2 dogs and a mountain with a colour gradient).

new website: for new webpage I decided to have a navigation for each section of education. In the main area I would like to have some pictures to give an idea what content is behind. At the moment it looks terrible, so I decided to use you as support for me to make the webpage prettier :). And maybe you have an better idea how to make it great. -> current state of new web page: https://moluvo.perch-net.ch/

Target Market(s)

adult eduction for adult in safety at work, mountain climbing, dog school

Number of Pages Required

1 page

Font styles to use
Serif
Sans Serif

Requirements
Must have
• As main color is set "Ral 6011" (green) -> #6C7C59

```html
<!DOCTYPE html>
<html lang="en">
<head>
<meta charset="utf-8">
<title>moluvo – homepage layouts</title>
<link href="https://fonts.googleapis.com/css2?family=Lato:ital,wght@0,400;0,700;0,900;1,400&display=swap" rel="stylesheet">
<style>
:root{
  --green:#6C7C59;
  --green-dark:#5d6c4b;
  --ink:#1d1d1d;
  --muted:#6a6a6a;
  --line:#c9c9c9;
  --soft:#f6f6f6;
  --board:#ececec;
  --footer:#222222;
  --white:#ffffff;
}
*{box-sizing:border-box;margin:0;padding:0}
html,body{width:840px;height:1200px;overflow:hidden}
body{background:var(--board);font-family:'Lato',sans-serif;color:var(--ink);position:relative}
.page{position:absolute;top:35.5px;background:var(--white);transform:scale(.5227);transform-origin:0 0;overflow:hidden;height:2159px;box-shadow:0 2px 10px rgba(0,0,0,.08)}
.page--desktop{left:82px;width:629px}
.page--compact{left:500.2px;width:493px}
.abs{position:absolute}
.t{position:absolute;line-height:1;white-space:nowrap}
.center{left:0;right:0;text-align:center}
.brand{font-weight:700;color:var(--green);display:flex;align-items:center;gap:8px}
.brand i{display:block;border-radius:50%;background:var(--green)}
.topline{color:var(--ink);font-size:8px}
.topline b{color:var(--green);font-weight:400}
.nav{display:flex;font-size:9.5px;color:var(--ink)}
.photo{position:absolute}
.hero-photo{background:
  radial-gradient(ellipse 22% 30% at 72% 42%,rgba(230,120,40,.55),rgba(230,120,40,0) 70%),
  linear-gradient(180deg,#d9a77d 0%,#8fa3b8 20%,#3f5f7e 45%,#7d98b3 62%,#dfe7ef 82%,#f1f4f7 100%)}
.hero-title{color:var(--white);font-weight:900;text-transform:uppercase}
.pill{position:absolute;border-radius:20px;display:flex;align-items:center;justify-content:center;font-weight:700;text-transform:uppercase}
.pill--light{background:var(--white);color:var(--ink)}
.pill--green{background:var(--green);color:var(--white)}
.pill--dark{background:var(--footer);color:var(--white)}
.dots{position:absolute;display:flex;gap:3px}
.dots span{width:6px;height:6px;border-radius:50%;border:1px solid var(--white)}
.dots span:first-child{background:var(--white)}
.section-title{font-weight:900;text-transform:uppercase;color:var(--ink)}
.lead{color:var(--muted);text-align:center;line-height:1.45;white-space:normal}
.value-label{color:var(--ink);text-align:center;width:140px}
.courses-band{background:var(--soft);clip-path:polygon(0 35px,100% 0,100% 100%,0 100%)}
.course{position:absolute;width:165px;height:155px}
.course .photo{left:0;top:0;width:165px;height:155px}
.course-label{position:absolute;left:17px;top:124px;width:140px;height:36px;background:var(--white);box-shadow:0 2px 6px rgba(0,0,0,.15);display:flex;align-items:center;justify-content:center;font-size:12px;color:var(--ink)}
.course-label--active{background:var(--green);color:var(--white)}
.body-copy{color:var(--muted);line-height:1.55;white-space:nowrap}
.testimonial-band{background:var(--green);clip-path:polygon(0 50px,100% 0,100% 205px,0 242px)}
.avatar{position:absolute;border-radius:50%;background:#d9d9d9;border:3px solid var(--white);overflow:hidden}
.avatar::before{content:"";position:absolute;left:50%;top:20%;width:34%;height:34%;transform:translateX(-50%);border-radius:50%;background:var(--white)}
.avatar::after{content:"";position:absolute;left:50%;top:58%;width:70%;height:60%;transform:translateX(-50%);border-radius:50% 50% 0 0;background:var(--white)}
.quote{color:var(--white);font-style:italic;line-height:1.45;white-space:nowrap}
.field{position:absolute;border:1px solid var(--line);background:var(--white);color:var(--muted);padding:7px 8px}
.info-icon{position:absolute;border-radius:50%;border:1.5px solid var(--green)}
.info-label{font-weight:700;text-transform:uppercase}
.footer-band{background:var(--footer)}
.social{position:absolute;border-radius:50%;border:1.5px solid var(--white)}
.footer-links{color:var(--white)}
.topic{position:absolute;overflow:hidden}
.topic-copy{color:var(--muted);line-height:1.6;white-space:nowrap}
.item{position:absolute;display:flex;align-items:center;gap:6px;color:var(--ink);line-height:1.25}
.item svg{flex:none}
</style>
</head>
<body>

<svg width="0" height="0" style="position:absolute" aria-hidden="true">
  <defs>
    <symbol id="ring" viewBox="0 0 36 36">
      <circle cx="18" cy="18" r="16.5" fill="#fff" stroke="#8a8a8a" stroke-width="1"/>
      <circle cx="18" cy="13" r="3.2" fill="#6C7C59"/>
      <path d="M11.5 26c0-4.5 3-7.5 6.5-7.5s6.5 3 6.5 7.5z" fill="#6C7C59"/>
    </symbol>
    <symbol id="value" viewBox="0 0 72 72">
      <circle cx="36" cy="36" r="34.5" fill="#fff" stroke="#bdbdbd" stroke-width="1"/>
      <circle cx="36" cy="36" r="29" fill="#fff" stroke="#6C7C59" stroke-width="3.5"/>
    </symbol>
  </defs>
</svg>

<!-- ================= DESKTOP LAYOUT ================= -->
<main class="page page--desktop">
  <header>
    <div class="abs brand" style="left:58px;top:20px;font-size:24px"><i style="width:14px;height:14px"></i>moluvo.ch</div>
    <div class="t topline" style="left:405px;top:15px">+41 79 512 08 47 &nbsp;|&nbsp; <b>✉</b> info@moluvo.ch</div>
    <nav class="t nav" style="left:223px;top:41px;gap:12px">
      <span>Occupational safety</span><span>First aid</span><span>Dog training</span><span>CZV</span><span>Mountain training</span><span>About</span>
    </nav>
  </header>

  <section>
    <div class="photo hero-photo" role="img" aria-label="Climber in an orange jacket on a snowy ridge at sunrise" style="left:0;top:63px;width:629px;height:304px;clip-path:polygon(0 0,100% 0,100% 274px,0 304px)"></div>
    <h1 class="t hero-title" style="left:59px;top:150px;font-size:25px;line-height:1.18">Your training and<br>course partner</h1>
    <div class="pill pill--light" style="left:59px;top:222px;width:85px;height:27px;font-size:8px;font-weight:400">Contact us</div>
    <div class="dots" style="left:297px;top:319px"><span></span><span></span><span></span><span></span></div>
  </section>

  <section>
    <h2 class="t center section-title" style="top:392px;font-size:23px">Welcome to moluvo</h2>
    <p class="t center lead" style="top:428px;font-size:10px">Adult eduction for adult in safety at work, mountain climbing,<br>dog school, various courses in different areas.</p>
    <svg class="abs" style="left:58px;top:480px" width="514" height="70" viewBox="0 0 514 70" aria-hidden="true">
      <line x1="0" y1="47" x2="514" y2="13" stroke="#bdbdbd" stroke-width="1"/>
    </svg>
    <svg class="abs" style="left:82px;top:486px" width="72" height="72" aria-hidden="true"><use href="#value"/><circle cx="36" cy="36" r="11" fill="none" stroke="#6C7C59" stroke-width="7" stroke-dasharray="4 2.6"/><circle cx="36" cy="36" r="5" fill="#6C7C59"/></svg>
    <svg class="abs" style="left:214px;top:478px" width="72" height="72" aria-hidden="true"><use href="#value"/><circle cx="36" cy="36" r="15" fill="none" stroke="#6C7C59" stroke-width="3"/><circle cx="36" cy="36" r="8" fill="none" stroke="#6C7C59" stroke-width="3"/><circle cx="36" cy="36" r="2.5" fill="#6C7C59"/><path d="M36 36L49 23" stroke="#6C7C59" stroke-width="2.5"/></svg>
    <svg class="abs" style="left:345px;top:469px" width="72" height="72" aria-hidden="true"><use href="#value"/><path d="M27 51v-6c-4-3-6-7-5-12 1-7 7-11 14-10 7 1 11 7 10 13l3 5-3 1v5h-6v4" fill="none" stroke="#6C7C59" stroke-width="2.2"/><circle cx="36" cy="31" r="4.5" fill="none" stroke="#6C7C59" stroke-width="2.2"/></svg>
    <svg class="abs" style="left:477px;top:462px" width="72" height="72" aria-hidden="true"><use href="#value"/><path d="M36 20l13 5v10c0 9-6 15-13 18-7-3-13-9-13-18V25z" fill="#6C7C59"/><path d="M29 36l5 5 9-10" fill="none" stroke="#fff" stroke-width="3"/></svg>
    <div class="t value-label" style="left:48px;top:568px;font-size:12px">Professional</div>
    <div class="t value-label" style="left:180px;top:560px;font-size:12px">Goal-oriented</div>
    <div class="t value-label" style="left:311px;top:551px;font-size:12px">Skills &amp; knowledge</div>
    <div class="t value-label" style="left:443px;top:545px;font-size:12px">Safety</div>
  </section>

  <section>
    <div class="abs courses-band" style="left:0;top:590px;width:629px;height:697px"></div>
    <h2 class="t center section-title" style="top:648px;font-size:21px">Training courses</h2>

    <div class="course" style="left:59px;top:696px"><div class="photo" role="img" aria-label="Forklift instructor with trainee in hard hat" style="background:linear-gradient(135deg,#5a4a3d,#b8a070 55%,#d6d24a)"></div><div class="course-label">Forklift courses</div></div>
    <div class="course" style="left:233px;top:696px"><div class="photo" role="img" aria-label="Fall protection harness being fitted" style="background:linear-gradient(135deg,#9fb5a8,#c9803a 50%,#2e3b52)"></div><div class="course-label course-label--active">PSAgA courses</div></div>
    <div class="course" style="left:406px;top:696px"><div class="photo" role="img" aria-label="Aerial work platform against blue sky" style="background:linear-gradient(180deg,#2f66a8,#6b9ad0 55%,#c67a2b)"></div><div class="course-label">Aerial work platform</div></div>

    <div class="course" style="left:59px;top:877px"><div class="photo" role="img" aria-label="Rescue dog team beside vehicle and helicopter" style="background:linear-gradient(180deg,#8a93a0,#b9bcbf 45%,#6b5a4a)"></div><div class="course-label">Dog training</div></div>
    <div class="course" style="left:233px;top:877px"><div class="photo" role="img" aria-label="People practising CPR on training mannequin" style="background:linear-gradient(135deg,#e8e4df,#c9a58c 50%,#8aa3b8)"></div><div class="course-label">Emergency helper</div></div>
    <div class="course" style="left:406px;top:877px"><div class="photo" role="img" aria-label="Paramedics in red treating a patient" style="background:linear-gradient(135deg,#6a6f78,#c8342c 50%,#4a4e57)"></div><div class="course-label">Medical training</div></div>

    <div class="course" style="left:59px;top:1058px"><div class="photo" role="img" aria-label="Green regional train at platform" style="background:linear-gradient(180deg,#c9cdd2,#7ab03a 55%,#4d4d4d)"></div><div class="course-label">TRS AGD</div></div>
    <div class="course" style="left:233px;top:1058px"><div class="photo" role="img" aria-label="Black truck under blue sky" style="background:linear-gradient(180deg,#3a6fb0,#7aa55a 45%,#1c1c1c)"></div><div class="course-label">CZV</div></div>
    <div class="course" style="left:406px;top:1058px"><div class="photo" role="img" aria-label="Climbers on a rocky mountain ridge" style="background:linear-gradient(135deg,#b9c3cc,#7c7770 50%,#a33a3a)"></div><div class="course-label">Mountain training</div></div>
  </section>

  <section>
    <h2 class="t section-title" style="left:59px;top:1320px;font-size:22px">About us</h2>
    <p class="t body-copy" style="left:59px;top:1360px;font-size:8.7px">In my professional career, I repeatedly experienced situations<br>that made me mature the idea of providing every interested<br>person witha basic knowledge that allows him to react<br>correctly and with the necessary calmness in an emergency<br>situation. The pooling &amp; combining knowledge and skills<br>of the different departments gives people security and<br>confidence in his actions.</p>
    <div class="pill pill--green" style="left:59px;top:1473px;width:79px;height:27px;font-size:9px;font-weight:400">Read more</div>
    <div class="photo" role="img" aria-label="Two instructors seated outdoors with their dogs under autumn trees" style="left:334px;top:1298px;width:237px;height:218px;clip-path:polygon(0 0,100% 0,100% 96%,0 100%);background:linear-gradient(160deg,#6b7d92,#8c6a3f 45%,#3e3a30)"></div>
  </section>

  <section>
    <div class="abs testimonial-band" style="left:0;top:1530px;width:629px;height:245px"></div>
    <h2 class="t center section-title" style="top:1587px;font-size:20px;color:var(--white)">Testimonials</h2>
    <div class="avatar" style="left:59px;top:1602px;width:92px;height:92px"></div>
    <div class="abs" style="left:173px;top:1638px;width:1px;height:62px;background:var(--white)"></div>
    <p class="t quote" style="left:208px;top:1637px;font-size:9.6px">“ Lorem ipsum dolor sit amet, consectetur adipiscing elit, sed do eiusmod tem<br>por incididunt ut labore et dolore magna aliqua. Ut enim ad minim veniam,<br>quis nostrud exercitation ullamco laboris nisi ut aliquip ex ea commodo cons<br>equat. Duis aute irure dolor in reprehenderit.”</p>
    <div class="t" style="left:208px;top:1711px;font-size:10px;color:var(--white)">- JOHN DOE</div>
  </section>

  <section>
    <h2 class="t center section-title" style="top:1795px;font-size:22px">Contact us</h2>
    <div class="field" style="left:59px;top:1840px;width:156px;height:27px;font-size:8.5px">First Name</div>
    <div class="field" style="left:220px;top:1840px;width:156px;height:27px;font-size:8.5px">Last Name</div>
    <div class="field" style="left:59px;top:1873px;width:156px;height:27px;font-size:8.5px">Your Phone</div>
    <div class="field" style="left:220px;top:1873px;width:156px;height:27px;font-size:8.5px">Your Email</div>
    <div class="field" style="left:59px;top:1906px;width:317px;height:55px;font-size:8.5px">How can we help you?</div>
    <div class="pill pill--green" style="left:59px;top:1974px;width:75px;height:27px;font-size:9px">Submit</div>

    <div class="info-icon" style="left:404px;top:1838px;width:28px;height:28px"></div>
    <svg class="abs" style="left:413px;top:1845px" width="10" height="14" viewBox="0 0 10 14" aria-hidden="true"><path d="M5 13C2 9 1 7 1 5a4 4 0 018 0c0 2-1 4-4 8z" fill="none" stroke="#6C7C59" stroke-width="1.4"/><circle cx="5" cy="5" r="1.4" fill="#6C7C59"/></svg>
    <div class="t" style="left:445px;top:1839px;font-size:8.5px;line-height:1.35"><span class="info-label">Location</span><br><span style="color:var(--muted)">Lindenweg 27,<br>CH-3900 Brig</span></div>

    <div class="info-icon" style="left:404px;top:1893px;width:28px;height:28px"></div>
    <svg class="abs" style="left:412px;top:1901px" width="12" height="12" viewBox="0 0 12 12" aria-hidden="true"><path d="M2 1l2.5 0 1 3-1.5 1c.8 1.6 1.8 2.6 3.3 3.3l1-1.5 3 1V11C6 11 1 6 2 1z" fill="none" stroke="#6C7C59" stroke-width="1.2"/></svg>
    <div class="t" style="left:445px;top:1895px;font-size:8.5px;line-height:1.35"><span class="info-label">Call us</span><br><span style="color:var(--muted)">+41 79 512 08 47</span></div>

    <div class="info-icon" style="left:404px;top:1938px;width:28px;height:28px"></div>
    <svg class="abs" style="left:411px;top:1947px" width="14" height="10" viewBox="0 0 14 10" aria-hidden="true"><rect x="1" y="1" width="12" height="8" fill="#6C7C59"/><path d="M1 1l6 4.5L13 1" fill="none" stroke="#fff" stroke-width="1.2"/></svg>
    <div class="t" style="left:445px;top:1940px;font-size:8.5px;line-height:1.35"><span class="info-label">Email us</span><br><span style="color:var(--muted)">info@moluvo.ch</span></div>
  </section>

  <footer>
    <div class="abs footer-band" style="left:0;top:2008px;width:629px;height:151px;clip-path:polygon(0 42px,100% 0,100% 100%,0 100%)"></div>
    <div class="social" style="left:258px;top:2068px;width:24px;height:24px"></div>
    <div class="social" style="left:288px;top:2068px;width:24px;height:24px"></div>
    <div class="social" style="left:317px;top:2068px;width:24px;height:24px"></div>
    <div class="social" style="left:347px;top:2068px;width:24px;height:24px"></div>
    <div class="t center footer-links" style="top:2105px;font-size:8.8px">About &nbsp;| &nbsp;Occupational safety &nbsp;| &nbsp;Aerial work platform &nbsp;| &nbsp;First aid &nbsp;| &nbsp;Dog training &nbsp;| &nbsp;CZV &nbsp;| &nbsp;Mountain training</div>
    <div class="t center footer-links" style="top:2124px;font-size:8.8px">Copyright © 2021, moluvo. All rights reserved.</div>
  </footer>
</main>

<!-- ================= COMPACT LAYOUT ================= -->
<main class="page page--compact">
  <header>
    <div class="abs brand" style="left:46px;top:17px;font-size:17px;gap:6px"><i style="width:10px;height:10px"></i>moluvo.ch</div>
    <div class="t topline" style="left:316px;top:11px;font-size:6.5px">+41 79 512 08 47 &nbsp;|&nbsp; <b>✉</b> info@moluvo.ch</div>
    <nav class="t nav" style="left:145px;top:33px;gap:9px;font-size:7px">
      <span>Occupational safety</span><span>First aid</span><span>Dog training</span><span>CZV</span><span>Mountain training</span><span>About</span><span>Contact</span>
    </nav>
  </header>

  <section>
    <div class="photo hero-photo" role="img" aria-label="Climber in an orange jacket on a snowy ridge at sunrise" style="left:0;top:50px;width:493px;height:238px;clip-path:polygon(0 0,100% 0,100% 213px,0 238px)"></div>
    <h1 class="t hero-title" style="left:46px;top:116px;font-size:19px;line-height:1.18">Your training and<br>course partner</h1>
    <div class="pill pill--light" style="left:46px;top:174px;width:67px;height:21px;font-size:6.5px;font-weight:400">Contact us</div>
    <div class="dots" style="left:233px;top:250px"><span style="width:5px;height:5px"></span><span style="width:5px;height:5px"></span><span style="width:5px;height:5px"></span><span style="width:5px;height:5px"></span></div>
  </section>

  <section>
    <h2 class="t center section-title" style="top:308px;font-size:17px;font-weight:700">Welcome to moluvo</h2>
    <p class="t center lead" style="top:337px;font-size:7px">Adult eduction for adult in safety at work, mountain climbing,<br>dog school, various courses in different areas.</p>
    <svg class="abs" style="left:44px;top:380px" width="406" height="40" viewBox="0 0 406 40" aria-hidden="true"><line x1="0" y1="30" x2="406" y2="4" stroke="#bdbdbd" stroke-width="1"/></svg>
    <svg class="abs" style="left:64px;top:381px" width="56" height="56" viewBox="0 0 72 72" aria-hidden="true"><use href="#value"/><circle cx="36" cy="36" r="11" fill="none" stroke="#6C7C59" stroke-width="7" stroke-dasharray="4 2.6"/><circle cx="36" cy="36" r="5" fill="#6C7C59"/></svg>
    <svg class="abs" style="left:168px;top:375px" width="56" height="56" viewBox="0 0 72 72" aria-hidden="true"><use href="#value"/><circle cx="36" cy="36" r="15" fill="none" stroke="#6C7C59" stroke-width="3"/><circle cx="36" cy="36" r="8" fill="none" stroke="#6C7C59" stroke-width="3"/><circle cx="36" cy="36" r="2.5" fill="#6C7C59"/></svg>
    <svg class="abs" style="left:272px;top:368px" width="56" height="56" viewBox="0 0 72 72" aria-hidden="true"><use href="#value"/><path d="M27 51v-6c-4-3-6-7-5-12 1-7 7-11 14-10 7 1 11 7 10 13l3 5-3 1v5h-6v4" fill="none" stroke="#6C7C59" stroke-width="2.2"/><circle cx="36" cy="31" r="4.5" fill="none" stroke="#6C7C59" stroke-width="2.2"/></svg>
    <svg class="abs" style="left:374px;top:363px" width="56" height="56" viewBox="0 0 72 72" aria-hidden="true"><use href="#value"/><path d="M36 20l13 5v10c0 9-6 15-13 18-7-3-13-9-13-18V25z" fill="#6C7C59"/><path d="M29 36l5 5 9-10" fill="none" stroke="#fff" stroke-width="3"/></svg>
    <div class="t value-label" style="left:22px;top:446px;font-size:8.5px">Professional</div>
    <div class="t value-label" style="left:126px;top:439px;font-size:8.5px">Goal-oriented</div>
    <div class="t value-label" style="left:230px;top:432px;font-size:8.5px">Skills &amp; knowledge</div>
    <div class="t value-label" style="left:332px;top:427px;font-size:8.5px">Safety</div>
  </section>

  <!-- Occupational safety -->
  <section class="topic" style="left:0;top:478px;width:493px;height:246px;clip-path:polygon(0 10px,100% 0,100% 100%,0 100%)">
    <div class="photo" role="img" aria-label="Worker in helmet securing himself with rope and harness" style="left:0;top:0;width:300px;height:246px;background:linear-gradient(90deg,#5c5a48 0%,#8c8672 40%,#d8d2bf 70%,rgba(255,255,255,0) 100%)"></div>
  </section>
  <h2 class="t section-title" style="left:253px;top:507px;font-size:16px;font-weight:400;line-height:1.25">Occupational<br>safety</h2>
  <p class="t topic-copy" style="left:253px;top:559px;font-size:5.6px">Nemo enim ipsam voluptatem quia voluptas sit aspernatur<br>aut odit aut fugit, sed quia conseq.</p>
  <div class="item" style="left:253px;top:590px;font-size:7px"><svg width="32" height="32"><use href="#ring"/></svg>Foreman</div>
  <div class="item" style="left:372px;top:590px;font-size:7px"><svg width="32" height="32"><use href="#ring"/></svg>Aerial work<br>platform</div>
  <div class="item" style="left:253px;top:634px;font-size:7px"><svg width="32" height="32"><use href="#ring"/></svg>Personal protective<br>equipment against<br>falling</div>
  <div class="item" style="left:372px;top:634px;font-size:7px"><svg width="32" height="32"><use href="#ring"/></svg>Material<br>control</div>

  <!-- First aid -->
  <section class="topic" style="left:0;top:700px;width:493px;height:240px;clip-path:polygon(0 24px,100% 0,100% 92%,0 100%)">
    <div class="photo" role="img" aria-label="Hands performing chest compressions on a training mannequin" style="right:0;top:0;width:300px;height:240px;background:linear-gradient(270deg,#d9a998 0%,#e8cfc2 45%,#f1ebe7 75%,rgba(255,255,255,0) 100%)"></div>
  </section>
  <h2 class="t section-title" style="left:46px;top:755px;font-size:16px;font-weight:400">First aid</h2>
  <p class="t topic-copy" style="left:46px;top:784px;font-size:5.6px">Nemo enim ipsam voluptatem quia voluptas sit aspernatur<br>aut odit aut fugit, sed quia conseq.</p>
  <div class="item" style="left:46px;top:814px;font-size:7px"><svg width="32" height="32"><use href="#ring"/></svg>Emergency helper for driver's<br>license weavers</div>
  <div class="item" style="left:46px;top:857px;font-size:7px"><svg width="32" height="32"><use href="#ring"/></svg>Samaritan<br>training</div>

  <!-- Dog training -->
  <section class="topic" style="left:0;top:935px;width:493px;height:242px;clip-path:polygon(0 8%,100% 0,100% 92%,0 100%)">
    <div class="photo" role="img" aria-label="Handlers in winter jackets with a rescue dog in the snow" style="left:0;top:0;width:290px;height:242px;background:linear-gradient(90deg,#2c2a2a 0%,#6a5240 35%,#c9c6c2 70%,rgba(255,255,255,0) 100%)"></div>
  </section>
  <h2 class="t section-title" style="left:253px;top:965px;font-size:16px;font-weight:400">Dog training</h2>
  <p class="t topic-copy" style="left:253px;top:993px;font-size:5.6px">Nemo enim ipsam voluptatem quia voluptas sit aspernatur<br>aut odit aut fugit, sed quia conseq.</p>
  <div class="item" style="left:253px;top:1021px;font-size:7px"><svg width="32" height="32"><use href="#ring"/></svg>Theory before<br>buying a dog</div>
  <div class="item" style="left:372px;top:1021px;font-size:7px"><svg width="32" height="32"><use href="#ring"/></svg>Puppy<br>school</div>
  <div class="item" style="left:253px;top:1061px;font-size:7px"><svg width="32" height="32"><use href="#ring"/></svg>Mandatory rates<br>NHB</div>
  <div class="item" style="left:372px;top:1061px;font-size:7px"><svg width="32" height="32"><use href="#ring"/></svg>Welding<br>training</div>
  <div class="item" style="left:253px;top:1101px;font-size:7px"><svg width="32" height="32"><use href="#ring"/></svg>Avalanche<br>dog training</div>

  <!-- CZV -->
  <section class="topic" style="left:0;top:1155px;width:493px;height:245px;clip-path:polygon(0 9%,100% 0,100% 92%,0 100%)">
    <div class="photo" role="img" aria-label="Forklift trainee with instructor in hard hat" style="right:0;top:0;width:290px;height:245px;background:linear-gradient(270deg,#c9cf3a 0%,#8c7a5c 35%,#d9d4cc 70%,rgba(255,255,255,0) 100%)"></div>
  </section>
  <h2 class="t section-title" style="left:46px;top:1197px;font-size:16px;font-weight:400">CZV</h2>
  <p class="t topic-copy" style="left:46px;top:1226px;font-size:5.6px">Nemo enim ipsam voluptatem quia voluptas sit aspernatur<br>aut odit aut fugit, sed quia conseq.</p>
  <div class="item" style="left:46px;top:1258px;font-size:7px"><svg width="32" height="32"><use href="#ring"/></svg>Forklift courses</div>
  <div class="item" style="left:165px;top:1258px;font-size:7px"><svg width="32" height="32"><use href="#ring"/></svg>PSAgA</div>
  <div class="item" style="left:46px;top:1298px;font-size:7px"><svg width="32" height="32"><use href="#ring"/></svg>Aerial work<br>platform</div>
  <div class="item" style="left:165px;top:1298px;font-size:7px"><svg width="32" height="32"><use href="#ring"/></svg>1 help course</div>
  <div class="item" style="left:46px;top:1338px;font-size:7px"><svg width="32" height="32"><use href="#ring"/></svg>Snow-plowing<br>service</div>
  <div class="item" style="left:165px;top:1338px;font-size:7px"><svg width="32" height="32"><use href="#ring"/></svg>Fire<br>prevention</div>

  <!-- Mountain training -->
  <section class="topic" style="left:0;top:1398px;width:493px;height:242px;clip-path:polygon(0 6%,100% 0,100% 100%,0 100%)">
    <div class="photo" role="img" aria-label="Climber in yellow helmet clipping into rope on rock face" style="left:0;top:0;width:290px;height:242px;background:linear-gradient(90deg,#3d4a5c 0%,#7d7a70 35%,#d5d2cc 70%,rgba(255,255,255,0) 100%)"></div>
  </section>
  <h2 class="t section-title" style="left:253px;top:1437px;font-size:16px;font-weight:400">Mountain training</h2>
  <p class="t topic-copy" style="left:253px;top:1465px;font-size:5.6px">Nemo enim ipsam voluptatem quia voluptas sit aspernatur<br>aut odit aut fugit, sed quia conseq.</p>
  <div class="item" style="left:253px;top:1493px;font-size:7px"><svg width="32" height="32"><use href="#ring"/></svg>Basic training<br>summer</div>
  <div class="item" style="left:372px;top:1493px;font-size:7px"><svg width="32" height="32"><use href="#ring"/></svg>Ski<br>technique</div>
  <div class="item" style="left:253px;top:1538px;font-size:7px"><svg width="32" height="32"><use href="#ring"/></svg>Avalanche<br>courses</div>
  <div class="item" style="left:372px;top:1538px;font-size:7px"><svg width="32" height="32"><use href="#ring"/></svg>Alpine<br>rescue</div>

  <!-- About -->
  <section>
    <h2 class="t section-title" style="left:46px;top:1666px;font-size:16px;font-weight:700">About us</h2>
    <p class="t body-copy" style="left:46px;top:1696px;font-size:5.8px">In my professional career, I repeatedly experienced situations<br>that made me mature the idea of providing every interested<br>person witha basic knowledge that allows him to react<br>correctly and with the necessary calmness in an emergency<br>situation. The pooling &amp; combining knowledge and skills<br>of the different departments gives people security and<br>confidence in his actions.</p>
    <div class="pill pill--green" style="left:46px;top:1785px;width:72px;height:21px;font-size:6.5px;font-weight:400">Read more ⌄</div>
    <div class="photo" role="img" aria-label="Two instructors seated outdoors with their dogs under autumn trees" style="left:262px;top:1648px;width:186px;height:172px;clip-path:polygon(0 0,100% 0,100% 96%,0 100%);background:linear-gradient(160deg,#6b7d92,#8c6a3f 45%,#3e3a30)"></div>
  </section>

  <!-- Contact -->
  <section>
    <div class="abs" style="left:0;top:1828px;width:493px;height:250px;background:var(--green);clip-path:polygon(0 28px,100% 0,100% 215px,0 248px)"></div>
    <h2 class="t center section-title" style="top:1877px;font-size:16px;font-weight:700;color:var(--white)">Contact us</h2>
    <div class="field" style="left:46px;top:1912px;width:126px;height:20px;font-size:6px;padding:6px">First Name</div>
    <div class="field" style="left:179px;top:1912px;width:116px;height:20px;font-size:6px;padding:6px">Last Name</div>
    <div class="field" style="left:46px;top:1938px;width:126px;height:20px;font-size:6px;padding:6px">Your Phone</div>
    <div class="field" style="left:179px;top:1938px;width:116px;height:20px;font-size:6px;padding:6px">Your Email</div>
    <div class="field" style="left:46px;top:1964px;width:249px;height:41px;font-size:6px;padding:6px">How can we help you?</div>
    <div class="pill pill--dark" style="left:46px;top:2018px;width:58px;height:21px;font-size:6.5px;font-weight:400">Submit</div>

    <div class="info-icon" style="left:317px;top:1909px;width:22px;height:22px;border-color:var(--white)"></div>
    <div class="t" style="left:348px;top:1908px;font-size:6px;line-height:1.4;color:var(--white)"><span class="info-label" style="font-weight:400">Location</span><br>Lindenweg 27,<br>CH-3900 Brig</div>
    <div class="info-icon" style="left:317px;top:1953px;width:22px;height:22px;border-color:var(--white)"></div>
    <div class="t" style="left:348px;top:1953px;font-size:6px;line-height:1.4;color:var(--white)"><span class="info-label" style="font-weight:400">Call us</span><br>+41 79 512 08 47</div>
    <div class="info-icon" style="left:317px;top:1988px;width:22px;height:22px;border-color:var(--white)"></div>
    <div class="t" style="left:348px;top:1988px;font-size:6px;line-height:1.4;color:var(--white)"><span class="info-label" style="font-weight:400">Email us</span><br>info@moluvo.ch</div>
  </section>

  <footer>
    <div class="abs footer-band" style="left:0;top:2044px;width:493px;height:115px;clip-path:polygon(0 32px,100% 0,100% 100%,0 100%)"></div>
    <div class="social" style="left:201px;top:2091px;width:19px;height:19px"></div>
    <div class="social" style="left:225px;top:2091px;width:19px;height:19px"></div>
    <div class="social" style="left:249px;top:2091px;width:19px;height:19px"></div>
    <div class="social" style="left:272px;top:2091px;width:19px;height:19px"></div>
    <div class="t center footer-links" style="top:2119px;font-size:6px">About &nbsp;| &nbsp;Occupational safety &nbsp;| &nbsp;Aerial work platform &nbsp;| &nbsp;First aid &nbsp;| &nbsp;Dog training &nbsp;| &nbsp;CZV &nbsp;| &nbsp;Mountain training</div>
    <div class="t center footer-links" style="top:2134px;font-size:6px">Copyright © 2021, moluvo. All rights reserved.</div>
  </footer>
</main>

</body>
</html>
```